fernwick study hub community

The website presents a new interactive learning system where it provides not only the teaching material as the instructor friend who can both teach and learn, making friends and making money.
Make friends and get money.

```html
<!DOCTYPE html>
<html lang="en">
<head>
<meta charset="utf-8">
<title>Fernwick Study Hub</title>
<link href="https://fonts.googleapis.com/css2?family=Open+Sans:ital,wght@0,400;0,600;0,700;1,400&display=swap" rel="stylesheet">
<style>
:root{
  --ink:#0c0f1a;
  --blue:#0a8fd6;
  --text:#2a2a2a;
  --muted:#8a8a8a;
  --grey-band:#f3f3f3;
  --white:#ffffff;
}
*{margin:0;padding:0;box-sizing:border-box}
html,body{width:769px;height:1200px;overflow:hidden;background:var(--white)}
body{font-family:"Open Sans",Arial,sans-serif;color:var(--text);position:relative}
.site-header{position:absolute;left:0;top:0;width:769px;height:46px;background:var(--ink)}
.brand{position:absolute;left:63px;top:12px;color:var(--white);font-weight:700;font-size:16px;letter-spacing:.5px;display:flex;align-items:center;gap:6px}
.brand-dot{width:9px;height:9px;border-radius:50%;background:var(--blue)}
.main-nav{position:absolute;top:18px;left:0;font-size:7.5px;color:#d8d8d8;letter-spacing:.2px}
.main-nav a{position:absolute;white-space:nowrap;color:inherit;text-decoration:none}
.main-nav a.is-active{color:var(--blue)}
.login-btn{position:absolute;left:650px;top:12px;width:56px;height:22px;background:var(--blue);color:var(--white);font-size:7.5px;display:flex;align-items:center;justify-content:center;gap:4px;border-radius:2px}
.hero{position:absolute;left:0;top:46px;width:769px;height:403px;background:linear-gradient(180deg,#7c8d5a 0%,#a7a184 35%,#8e7b5e 65%,#6e6a36 100%)}
.hero-title{position:absolute;left:0;width:769px;top:356px;text-align:center;color:var(--white);font-weight:700;font-size:36px;letter-spacing:.5px;text-shadow:0 1px 3px rgba(0,0,0,.35)}
.hero-sub{position:absolute;left:0;width:769px;top:399px;text-align:center;color:var(--white);font-size:16px}
.section-title{position:absolute;left:0;width:769px;text-align:center;font-size:14px;color:var(--text);font-weight:400}
.section-title span{color:var(--blue)}
.lead{position:absolute;left:96px;width:577px;top:502px;text-align:center;font-size:7.4px;line-height:13.4px;color:#666}
.feature,.step{position:absolute;width:206px;text-align:center}
.feature-mark{display:block;width:50px;height:50px;border-radius:50%;background:var(--blue);margin:14px auto 0}
.feature h3,.step h3{font-weight:400;font-size:12.5px;color:var(--text);margin-bottom:6px}
.feature p,.step p{font-size:6.6px;line-height:12px;color:var(--muted)}
.works{position:absolute;left:0;top:734px;width:769px;height:184px;background:var(--grey-band)}
.cta{position:absolute;left:335px;top:866px;width:90px;height:27px;background:var(--blue);color:var(--white);font-size:8.5px;font-weight:600;display:flex;align-items:center;justify-content:center}
.quote{position:absolute;left:130px;width:509px;top:942px;text-align:center;font-style:italic;font-size:10px;line-height:17px;color:#666}
.quote-name{position:absolute;left:0;width:769px;top:983px;text-align:center;font-size:9.5px;font-weight:600}
.member-strip{position:absolute;left:73px;top:1009px;width:624px;height:28px;background:linear-gradient(90deg,#fff 0%,#b89a86 6%,#8d7a6c 30%,#a58b7a 55%,#6f5d52 75%,#a9928a 95%,#fff 100%)}
.contact-sub{position:absolute;left:0;width:769px;top:1091px;text-align:center;font-size:8.5px;color:#666}
.social{position:absolute;top:1116px;left:314px;display:flex;gap:6px}
.social span{width:18px;height:18px;border-radius:50%;background:#cfcfcf}
.social span.is-hover{background:var(--blue)}
.site-footer{position:absolute;left:0;top:1153px;width:769px;height:47px;background:var(--ink);color:#9a9a9a;font-size:7px;text-align:center;padding-top:15px}
</style>
</head>
<body>
<header class="site-header">
  <div class="brand">FERNWICK <span class="brand-dot"></span></div>
  <nav class="main-nav">
    <a class="is-active" style="left:264px">HOME</a>
    <a style="left:316px">ABOUT US</a>
    <a style="left:384px">HOW IT WORKS</a>
    <a style="left:472px">WHAT WE DO</a>
    <a style="left:552px">CONTACT US</a>
  </nav>
  <div class="login-btn"><svg width="7" height="7" viewBox="0 0 10 10"><circle cx="5" cy="3" r="2.4" fill="#fff"/><path d="M0.5 10c0-3 2-4.5 4.5-4.5S9.5 7 9.5 10z" fill="#fff"/></svg>LOGIN</div>
</header>

<section class="hero" role="img" aria-label="Photo of young friends sitting on grass studying together on a tablet"></section>
<h1 class="hero-title">WELCOME TO FERNWICK</h1>
<p class="hero-sub">We have created new&nbsp; interactive learning system.</p>

<h2 class="section-title" style="top:474px">BY MAKING FRIENDS <span>YOU CAN MAKE MONEY</span></h2>
<p class="lead">Proin leo odio, dignissim at euismod nec, consectetur vulputate diam. Morbi elementum ante at lacus finibus elementum. In viverra mauris ac sapien molestie, quis faucibus diam hendrerit. Aliquam et neque et neque feugiat volutpat sit amet ut erat. Morbi nec ultricies metus. Proin suscipit turpis nec placerat elementum. Morbi faucibus libero eu egestas bibendum. Morbi dignissim metus ut tristique tristique. Quisque ac augue at magna laoreet dignissim.</p>

<div class="feature" style="left:59px;top:563px">
  <span class="feature-mark"></span>
  <h3 style="margin-top:10px">Lorem Ipsum is simply</h3>
  <p>Proin leo odio, dignissim at euismod nec, consectetur vulputate diam. Morbi elementum ante at lacus finibus elementum. In viverra mauris ac sapien molestie.</p>
</div>
<div class="feature" style="left:278px;top:563px">
  <span class="feature-mark"></span>
  <h3 style="margin-top:10px">Lorem Ipsum is simply</h3>
  <p>Proin leo odio, dignissim at euismod nec, consectetur vulputate diam. Morbi elementum ante at lacus finibus elementum. In viverra mauris ac sapien molestie.</p>
</div>
<div class="feature" style="left:500px;top:563px">
  <span class="feature-mark"></span>
  <h3 style="margin-top:10px">Lorem Ipsum is simply</h3>
  <p>Proin leo odio, dignissim at euismod nec, consectetur vulputate diam. Morbi elementum ante at lacus finibus elementum. In viverra mauris ac sapien molestie.</p>
</div>

<section class="works"></section>
<h2 class="section-title" style="top:757px">HOW IT <span>WORKS</span></h2>
<div class="step" style="left:59px;top:790px"><h3>1. Sed ut perspiciatis unde</h3><p>Proin leo odio, dignissim at euismod nec, consectetur vulputate diam. Morbi elementum ante at lacus finibus elementum. In viverra mauris ac sapien molestie.</p></div>
<div class="step" style="left:280px;top:790px"><h3>1. Sed ut perspiciatis unde</h3><p>Proin leo odio, dignissim at euismod nec, consectetur vulputate diam. Morbi elementum ante at lacus finibus elementum. In viverra mauris ac sapien molestie.</p></div>
<div class="step" style="left:502px;top:790px"><h3>1. Sed ut perspiciatis unde</h3><p>Proin leo odio, dignissim at euismod nec, consectetur vulputate diam. Morbi elementum ante at lacus finibus elementum. In viverra mauris ac sapien molestie.</p></div>
<div class="cta">GET PAID</div>

<p class="quote">“Lorem ipsum dolor sit amet, consectetur adipiscing elit. Mauris interdum velit vitae nulla molestie eu commodo nulla dapib us. Donec id sollicitudin urna. Integer at dui ac leo fermentum varius eleifend ut.”</p>
<p class="quote-name">Mara Quill</p>
<div class="member-strip" role="img" aria-label="Row of small member portrait photos"></div>

<h2 class="section-title" style="top:1066px">SAY HI &amp; <span>GET IN TOUCH</span></h2>
<p class="contact-sub">Lorem ipsum dolor sit amet, consectetur adipiscing elit suspendisse.</p>
<div class="social" aria-label="Social links"><span></span><span></span><span class="is-hover"></span><span></span><span></span><span></span></div>

<footer class="site-footer">Copyright © 2014&nbsp; Fernwick Study Hub all copyrights are reserved</footer>
</body>
</html>
```